Website Design for a holiday home letting busines

We require a redesign of our present website www.pinebrookstays.com. We want the website to stand out and look professional and clean to make holiday hunters want to book a caravan or lodge holiday with us. Our logo is red however we DO NOT want the website to be red. We want a natural colour scheme.

The final design should communicate that we are a professional company to book with.

On the home page we require;
Overview of company
Photo
Search box for holiday (check in)
Late Deals
Reviews
News

We would like the following pages designed; home page, available dates page, caravans page, content page.

The website should be responsive for smart phones. One website I do like is http://www.verdoliso.be/nl/

Target Market(s)

Families

Industry/Entity Type

Travel

Number of Pages Required

5+ page

Font styles to use
Serif

Requirements
Must have
• The project must be responsive for mobile phones and tablets.
• Ability to search for holiday home holidays
• We want a natural colour scheme.
Nice to have
• A style we like is http://www.verdoliso.be/nl/
Should not have
• Do not use red as a colour for the website. Our logo is red so this is the only time we want this used.

```html
<!DOCTYPE html>
<html lang="en">
<head>
<meta charset="utf-8">
<title>Pinebrook Stays – Caravan and Lodge Holidays</title>
<link href="https://fonts.googleapis.com/css2?family=Lora:wght@400;700&family=Open+Sans:wght@400;600&display=swap" rel="stylesheet">
<style>
:root{
  --teal:#5cc9c9;
  --teal-dark:#3fb0b2;
  --teal-pale:#dcf3f3;
  --teal-mist:#eefafa;
  --grey-nav:#9b9b9b;
  --grey-foot:#8c8c8c;
  --grey-bar:#6f6f6f;
  --ink:#6d6d6d;
  --ink-soft:#a4a4a4;
  --logo:#d9585b;
  --white:#ffffff;
}
*{box-sizing:border-box;margin:0;padding:0}
html,body{width:1200px;height:3288px;overflow:hidden}
body{position:relative;background:var(--white);font-family:"Open Sans",Arial,sans-serif;color:var(--ink)}
.abs{position:absolute}
h2,h3,.serif{font-family:"Lora",Georgia,serif}

/* header */
.site-header{left:0;top:0;width:1200px;height:96px;background:var(--white)}
.brand{left:120px;top:18px;display:flex;align-items:center;gap:12px}
.brand-mark{width:44px;height:44px;background:var(--logo)}
.brand-name{font-family:"Lora",Georgia,serif;font-size:28px;color:var(--logo);font-weight:700}
.brand-tag{left:176px;top:62px;font-size:12px;color:var(--ink-soft)}
.contact-top{top:34px;display:flex;align-items:center;gap:10px;font-size:14px;color:var(--ink-soft)}
.contact-top .dot{width:28px;height:28px;border-radius:50%;background:var(--teal-pale);display:flex;align-items:center;justify-content:center}
.main-nav{left:180px;top:96px;width:1020px;height:48px;background:var(--grey-nav);display:flex;align-items:center;padding-left:14px;gap:30px}
.main-nav a{color:var(--white);font-size:14px;text-decoration:none}
.main-nav a.active{background:#b6b6b6;padding:14px 16px}

/* hero */
.hero{left:0;top:144px;width:1200px;height:556px;background:linear-gradient(100deg,#8fd3d2 0%,#b9e4e2 35%,#a6dcda 60%,#d8efed 100%)}
.hero-caption{left:240px;top:210px;font-family:"Lora",Georgia,serif;font-size:40px;color:var(--white)}
.hero-arrow{top:240px;width:34px;height:60px;background:rgba(255,255,255,.5);display:flex;align-items:center;justify-content:center}

/* search */
.search-band{left:0;top:700px;width:1200px;height:100px;background:var(--teal-pale)}
.field{top:32px;height:40px;background:var(--white);border:1px solid #cfe8e8;font-size:13px;color:var(--ink-soft);padding:11px 14px}
.btn{background:var(--teal);color:var(--white);font-size:13px;text-align:center;letter-spacing:.5px}

/* overview */
.section-title{font-family:"Lora",Georgia,serif;font-size:26px;color:var(--ink);text-transform:uppercase}
.overview-title{left:0;top:872px;width:1200px;text-align:center}
.overview-text{left:132px;top:930px;width:936px;text-align:center;font-size:13px;line-height:26px;color:var(--ink-soft)}
.overview-btn{left:530px;top:1068px;width:140px;height:36px;line-height:36px;box-shadow:0 2px 4px rgba(0,0,0,.15)}

/* stays */
.stays{left:0;top:1180px;width:1200px;height:600px;background:var(--teal-pale)}
.stays-title{left:132px;top:84px}
.stay-card{top:160px;width:296px;height:400px;background:var(--white)}
.stay-photo{left:0;top:0;width:296px;height:180px}
.stay-name{left:0;top:204px;width:296px;text-align:center;font-family:"Lora",Georgia,serif;font-size:18px;text-transform:uppercase}
.stay-text{left:24px;top:236px;width:248px;text-align:center;font-size:12px;line-height:20px;color:var(--ink-soft)}
.stay-meta{left:24px;top:296px;width:248px;display:flex;justify-content:space-between;font-size:11px;color:var(--ink-soft)}
.stay-btn{left:0;top:350px;width:296px;height:34px;line-height:34px}

/* deals */
.deals-title{left:132px;top:1864px}
.deal{top:1932px;width:276px}
.deal-photo{width:276px;height:248px;border-radius:0 0 24px 24px}
.deal-name{margin-top:26px;text-align:center;font-family:"Lora",Georgia,serif;font-size:17px;text-transform:uppercase}
.deal-sub{margin-top:10px;text-align:center;font-size:12px;color:var(--teal-dark);text-transform:uppercase}
.deal-meta{margin-top:16px;display:flex;justify-content:space-between;font-size:11px;color:var(--ink-soft);padding:0 14px}
.book-now{left:78px;top:112px;width:120px;height:34px;line-height:34px}

/* feeds */
.feed{top:2368px;width:296px;height:496px;background:var(--white);border:1px solid #d7eeee}
.feed-head{height:38px;line-height:38px;background:var(--teal);color:var(--white);text-align:center;font-family:"Lora",Georgia,serif;font-size:15px;text-transform:uppercase}
.feed-item{display:flex;gap:12px;padding:22px 16px 0}
.thumb{flex:none;width:72px;height:60px}
.feed-item h3{font-size:14px;color:var(--teal-dark);text-transform:uppercase;font-weight:400}
.feed-item p{font-size:11px;line-height:18px;color:var(--ink-soft);margin-top:6px}
.fb-brand{display:flex;align-items:center;gap:10px;padding:20px 16px}
.fb-brand .mark{width:40px;height:40px;border-radius:50%;background:var(--logo)}
.fb-brand span{font-family:"Lora",Georgia,serif;font-size:16px;color:var(--logo);font-weight:700}
.fb-grid{display:grid;grid-template-columns:repeat(4,56px);gap:8px;padding:14px 16px}
.fb-grid div{height:56px;background:linear-gradient(135deg,#c9dcdc,#9cc3c4)}

/* footer */
.site-footer{left:0;top:2932px;width:1200px;height:316px;background:var(--grey-foot);color:var(--white)}
.footer-col{top:44px}
.footer-col h2{font-size:20px;font-weight:400;margin-bottom:16px}
.footer-col p,.footer-col a{display:block;font-size:12px;line-height:22px;color:var(--white);text-decoration:none}
.news-input{width:210px;height:28px;background:var(--white)}
.social{display:flex;gap:8px;margin-top:10px}
.social span{width:24px;height:24px;border-radius:50%;background:#b9b9b9}
.bottom-bar{left:0;top:3248px;width:1200px;height:40px;background:var(--grey-bar);font-size:11px;color:#d8d8d8;padding:13px 132px;display:flex;justify-content:space-between}

/* modal */
.veil{left:0;top:0;width:1200px;height:3288px;background:rgba(255,255,255,.42)}
.modal{left:320px;top:272px;width:560px;height:248px;border:3px solid #444;background:linear-gradient(120deg,#c9b08f,#e6d6bf 50%,#b79a7a)}
.modal h2{position:absolute;left:0;top:40px;width:100%;text-align:center;font-size:24px;color:#333;letter-spacing:2px}
.modal-input{left:150px;top:92px;width:260px;height:36px;background:var(--white);font-size:12px;color:var(--ink-soft);padding:10px 12px}
.modal-send{left:220px;top:150px;width:120px;height:36px;line-height:36px;font-size:14px;font-weight:600}
.modal-close{left:524px;top:12px;width:22px;height:22px;background:#222}
</style>
</head>
<body>

<header class="site-header abs">
  <div class="brand abs"><span class="brand-mark"></span><span class="brand-name">Pinebrook Stays</span></div>
  <div class="brand-tag abs">Caravan &amp; Lodge Holiday Homes</div>
  <div class="contact-top abs" style="left:680px"><span class="dot"><svg width="14" height="14" viewBox="0 0 24 24"><path d="M6 2l4 4-2 3a12 12 0 0 0 7 7l3-2 4 4-3 4C10 22 2 14 2 5z" fill="#5cc9c9"/></svg></span>01632 960 482</div>
  <div class="contact-top abs" style="left:860px"><span class="dot"><svg width="14" height="14" viewBox="0 0 24 24"><rect x="2" y="5" width="20" height="14" fill="none" stroke="#5cc9c9" stroke-width="2"/><path d="M2 5l10 8 10-8" fill="none" stroke="#5cc9c9" stroke-width="2"/></svg></span>info@pinebrookstays.com</div>
</header>

<nav class="main-nav abs">
  <a class="active" href="#">Home</a><a href="#">Reviews</a><a href="#">Caravans &amp; Lodges</a><a href="#">Self Catering</a><a href="#">Offers</a><a href="#">Holiday Parks</a><a href="#">Suggested Links</a><a href="#">Location/Contact</a>
</nav>

<section class="hero abs" role="img" aria-label="Photo of a timber holiday lodge beside a birch tree">
  <div class="hero-caption abs">Private Holiday Lodges</div>
  <div class="hero-arrow abs" style="left:12px"><svg width="14" height="24"><path d="M12 2L2 12l10 10" stroke="#fff" stroke-width="3" fill="none"/></svg></div>
  <div class="hero-arrow abs" style="left:1154px"><svg width="14" height="24"><path d="M2 2l10 10L2 22" stroke="#fff" stroke-width="3" fill="none"/></svg></div>
</section>

<section class="search-band abs">
  <div class="field abs" style="left:132px;width:300px">Check in date</div>
  <div class="field abs" style="left:480px;width:340px">Number of nights</div>
  <div class="btn abs" style="left:880px;top:32px;width:188px;height:40px;line-height:40px">CHECK AVAILABILITY</div>
</section>

<h2 class="section-title overview-title abs">Overview of Company</h2>
<p class="overview-text abs">We are a family run business offering quality caravan and lodge holidays across the most beautiful parks in the country. Every home is cleaned, checked and ready for your arrival, with linen, towels and a welcome pack included. Whether you want a quiet break by the lake or a busy week of fun for the children, our friendly team will help you find the right stay. Browse our homes, check live availability and book online in minutes.</p>
<div class="btn overview-btn abs">VIEW MORE</div>

<section class="stays abs">
  <h2 class="section-title stays-title abs">Our Caravans and Lodges</h2>
  <article class="stay-card abs" style="left:132px">
    <div class="stay-photo abs" role="img" aria-label="Photo of a caravan lounge" style="background:linear-gradient(135deg,#d9cfc2,#efe8dd)"></div>
    <h3 class="stay-name abs">The Hollybrook</h3>
    <p class="stay-text abs">Three bedroom caravan with open plan lounge, sleeping six guests in comfort.</p>
    <div class="stay-meta abs"><span>Sleeps 6</span><span>3 Bedrooms</span><span>Pet friendly</span></div>
    <div class="btn stay-btn abs">VIEW MORE</div>
  </article>
  <article class="stay-card abs" style="left:452px">
    <div class="stay-photo abs" role="img" aria-label="Photo of a bright caravan living room" style="background:linear-gradient(135deg,#d6d9d2,#f2f0e8)"></div>
    <h3 class="stay-name abs">The Ashdown</h3>
    <p class="stay-text abs">Spacious lodge with decking and garden views, ideal for family breaks.</p>
    <div class="stay-meta abs"><span>Sleeps 6</span><span>2 Bedrooms</span><span>Decking</span></div>
    <div class="btn stay-btn abs">VIEW MORE</div>
  </article>
  <article class="stay-card abs" style="left:772px">
    <div class="stay-photo abs" role="img" aria-label="Photo of a caravan dining area" style="background:linear-gradient(135deg,#e3ddd3,#c9beb0)"></div>
    <h3 class="stay-name abs">The Larkfield</h3>
    <p class="stay-text abs">Modern caravan with a fitted kitchen and cosy seating for relaxed evenings.</p>
    <div class="stay-meta abs"><span>Sleeps 4</span><span>2 Bedrooms</span><span>Parking</span></div>
    <div class="btn stay-btn abs">VIEW MORE</div>
  </article>
</section>

<h2 class="section-title deals-title abs">Late Deals</h2>
<article class="deal abs" style="left:142px">
  <div class="deal-photo" role="img" aria-label="Photo of a caravan kitchen" style="background:linear-gradient(135deg,#9aa3a6,#d8dcdc)"></div>
  <div class="btn book-now abs">BOOK NOW</div>
  <h3 class="deal-name">The Marlowe</h3><p class="deal-sub">Seven nights from 14th August</p>
  <div class="deal-meta"><span>Sleeps 6</span><span>3 Beds</span><span>Save 20%</span></div>
</article>
<article class="deal abs" style="left:462px">
  <div class="deal-photo" role="img" aria-label="Photo of a caravan lounge with sofas" style="background:linear-gradient(135deg,#c8bfb2,#efe9e0)"></div>
  <h3 class="deal-name">The Marlowe</h3><p class="deal-sub">Four nights from 21st August</p>
  <div class="deal-meta"><span>Sleeps 6</span><span>3 Beds</span><span>Save 15%</span></div>
</article>
<article class="deal abs" style="left:782px">
  <div class="deal-photo" role="img" aria-label="Photo of a caravan kitchen and oven" style="background:linear-gradient(135deg,#e6e2dc,#b9b3ab)"></div>
  <h3 class="deal-name">The Marlowe</h3><p class="deal-sub">Three nights from 28th August</p>
  <div class="deal-meta"><span>Sleeps 6</span><span>3 Beds</span><span>Save 10%</span></div>
</article>

<section class="feed abs" style="left:132px">
  <h2 class="feed-head">Latest Reviews</h2>
  <div class="feed-item"><div class="thumb" role="img" aria-label="Guest photo" style="background:#cfe3e3"></div><div><h3>Eleanor Marsh</h3><p>A spotless caravan and a warm welcome. The children loved the park and we will be back next summer.</p></div></div>
  <div class="feed-item"><div class="thumb" role="img" aria-label="Guest photo" style="background:#cfe3e3"></div><div><h3>Tessa Whitfield</h3><p>Lovely lodge with everything we needed. Booking was easy and the team were helpful throughout.</p></div></div>
  <div class="feed-item"><div class="thumb" role="img" aria-label="Guest photo" style="background:#cfe3e3"></div><div><h3>Maria Holloway</h3><p>Great value for a family week away. Clean, comfortable and close to the beach and shops.</p></div></div>
</section>

<section class="feed abs" style="left:452px">
  <h2 class="feed-head">Blog Feed</h2>
  <div class="feed-item"><div class="thumb" role="img" aria-label="Blog photo of a lodge" style="background:#d8d2c8"></div><div><h3>Eleanor Marsh</h3><p>Our top tips for packing light on a caravan break with young children this summer.</p></div></div>
  <div class="feed-item"><div class="thumb" role="img" aria-label="Blog photo of a park" style="background:#d8d2c8"></div><div><h3>Tessa Whitfield</h3><p>Five family walks you can enjoy straight from the door of your holiday lodge.</p></div></div>
  <div class="feed-item"><div class="thumb" role="img" aria-label="Blog photo of a caravan" style="background:#d8d2c8"></div><div><h3>Maria Holloway</h3><p>New homes added for next season, with more space and pet friendly options.</p></div></div>
</section>

<section class="feed abs" style="left:772px">
  <h2 class="feed-head">Facebook Feed</h2>
  <div class="fb-brand"><span class="mark"></span><span>Pinebrook Stays</span></div>
  <div class="feed-item" style="padding-top:4px"><div class="thumb" role="img" aria-label="Post photo" style="background:#cfe3e3;width:60px;height:48px"></div><div><h3>Pinebrook Stays</h3><p>Late availability this weekend, book now.</p></div></div>
  <div class="feed-item"><div class="thumb" role="img" aria-label="Post photo" style="background:#cfe3e3;width:60px;height:48px"></div><div><p>Thank you to all our guests this season.</p></div></div>
  <p style="padding:18px 16px 0;font-size:12px;color:var(--teal-dark)">1,240 people like Pinebrook Stays</p>
  <div class="fb-grid" role="img" aria-label="Follower photos"><div></div><div></div><div></div><div></div><div></div><div></div><div></div><div></div></div>
</section>

<footer class="site-footer abs">
  <div class="footer-col abs" style="left:152px">
    <h2 class="serif">Contact us</h2>
    <p>Pinebrook Stays, Unit 4 Meadow Lane</p>
    <p>Ashford Business Park, AB1 2CD</p>
    <p style="margin-top:8px">01632 960 482</p>
    <p>info@pinebrookstays.com</p>
  </div>
  <div class="footer-col abs" style="left:480px">
    <h2 class="serif">Footer links</h2>
    <div style="display:flex;gap:60px"><div><a href="#">Home</a><a href="#">News</a><a href="#">Reviews</a><a href="#">Caravans &amp; Lodges</a><a href="#">Self Catering</a></div><div><a href="#">Suggested Links</a><a href="#">Location/Contact</a><a href="#">Offers</a></div></div>
  </div>
  <div class="footer-col abs" style="left:840px">
    <h2 class="serif">News letter</h2>
    <div class="news-input"></div>
    <div class="btn" style="width:110px;height:26px;line-height:26px;margin-top:8px;font-size:12px">SUBSCRIBE</div>
    <div class="social"><span></span><span></span><span></span><span></span></div>
  </div>
</footer>
<div class="bottom-bar abs"><span>© 2024 www.pinebrookstays.com</span><span>Top</span></div>

<div class="veil abs"></div>
<div class="modal abs" role="img" aria-label="Photo of a lodge bedroom behind the subscribe form">
  <div class="modal-close abs"><svg width="22" height="22"><path d="M6 6l10 10M16 6L6 16" stroke="#fff" stroke-width="2"/></svg></div>
  <h2 class="serif">SUBSCRIBE</h2>
  <div class="modal-input abs">Enter your email</div>
  <div class="btn modal-send abs">SEND</div>
</div>

</body>
</html>
```